Business Card Design for Marketing Firm

Looking for business card design for higher end marketing firm. Clean but impressionable/trendy. We are a marketing firm that represents manufacturers in the foodservice equipment and supply industry. Our customers are end users such has hotels, restaurants, country clubs, convention centers and casinos as well as distributors of restaurants supplies and equipment, and manufacturers of foodservice equipment and supplies.
Target Market(s)
Hotels, Restaurants, Supply & Equipment Distributors, Foodservice Manufacturers
Industry/Entity Type
Foodservice/Hospitality
Contact Information for Business Card
Name, Title, Contact Number, Email, Website, Social Media, Address
Requirements
Must have
- Clean & Simple but Serious and Impressionable

```html
<!DOCTYPE html>
<html lang="en">
<head>
<meta charset="utf-8">
<title>Meridian Service Reps – Business Cards</title>
<link rel="stylesheet" href="https://fonts.googleapis.com/css2?family=Montserrat:wght@400;500;700&display=swap">
<style>
  :root {
    --navy: #2a2c7b;
    --white: #ffffff;
    --backdrop: #e8e8ec;
    --ink-grey: #3a3a44;
    --card-shadow: 0 10px 28px rgba(20, 20, 50, 0.18);
  }
  * { margin: 0; padding: 0; box-sizing: border-box; }
  html, body {
    width: 1200px;
    height: 834px;
    overflow: hidden;
    background: var(--backdrop);
  }
  .stage {
    position: relative;
    width: 1200px;
    height: 834px;
  }
  .card {
    position: absolute;
    top: 262px;
    width: 540px;
    height: 309px;
    background: var(--white);
    box-shadow: var(--card-shadow);
    overflow: hidden;
  }
  .card--contact { left: 40px; }
  .card--brand { left: 620px; }

  .card__shapes {
    position: absolute;
    inset: 0;
    width: 100%;
    height: 100%;
  }

  /* Brand name with plain mark */
  .brand-name {
    position: absolute;
    display: flex;
    align-items: center;
    color: var(--navy);
    font-family: "Montserrat", Arial, sans-serif;
    font-weight: 500;
    text-transform: uppercase;
    white-space: nowrap;
    line-height: 1;
  }
  .brand-name__mark {
    flex: none;
    border-radius: 50%;
    background: var(--navy);
  }

  /* Brand side */
  .card--brand .brand-name {
    left: 60px;
    top: 120px;
    gap: 16px;
    font-size: 25px;
    letter-spacing: 1.5px;
  }
  .card--brand .brand-name__mark {
    width: 42px;
    height: 42px;
  }
  .social-row {
    position: absolute;
    left: 118px;
    top: 184px;
    display: flex;
    gap: 5px;
  }
  .social-row__dot {
    width: 13px;
    height: 13px;
    border-radius: 50%;
    background: var(--navy);
  }

  /* Contact side */
  .card--contact .brand-name {
    left: 30px;
    top: 36px;
    gap: 10px;
    font-size: 15px;
    letter-spacing: 1px;
  }
  .card--contact .brand-name__mark {
    width: 26px;
    height: 26px;
  }
  .person {
    position: absolute;
    right: 28px;
    top: 92px;
    text-align: right;
    font-family: "Montserrat", Arial, sans-serif;
  }
  .person__name {
    color: var(--navy);
    font-weight: 700;
    font-size: 21px;
    letter-spacing: 0.5px;
  }
  .person__title {
    color: var(--ink-grey);
    font-weight: 400;
    font-size: 13px;
    letter-spacing: 2px;
    margin-top: 3px;
  }
  .contact-list {
    position: absolute;
    right: 22px;
    top: 214px;
    list-style: none;
    font-family: "Montserrat", Arial, sans-serif;
    font-size: 12px;
    color: var(--white);
    text-align: right;
    line-height: 17px;
  }
  .contact-list__item {
    display: flex;
    justify-content: flex-end;
    align-items: center;
    gap: 7px;
  }
  .contact-list__icon {
    width: 11px;
    height: 11px;
    flex: none;
  }
  .contact-list__spacer {
    width: 11px;
    flex: none;
  }
</style>
</head>
<body>
<main class="stage">

  <!-- Contact side -->
  <section class="card card--contact" aria-label="Business card, contact side">
    <svg class="card__shapes" viewBox="0 0 540 309" preserveAspectRatio="none" aria-hidden="true">
      <path fill="var(--navy)" d="M0,120 C6,200 80,206 200,200 C330,193 450,178 540,186 L540,309 L0,309 Z"/>
      <path fill="none" stroke="var(--white)" stroke-width="2.5" d="M150,207 C290,196 430,186 540,198"/>
    </svg>

    <div class="brand-name">
      <span class="brand-name__mark" aria-hidden="true"></span>
      <span class="brand-name__text">Meridian Service Reps</span>
    </div>

    <div class="person">
      <div class="person__name">DANIEL WHITMORE</div>
      <div class="person__title">OWNER</div>
    </div>

    <ul class="contact-list">
      <li class="contact-list__item">Your address, City<span class="contact-list__spacer"></span></li>
      <li class="contact-list__item">State, Zip 1234<span class="contact-list__spacer"></span></li>
      <li class="contact-list__item">123 456 00000
        <svg class="contact-list__icon" viewBox="0 0 12 12" aria-hidden="true"><path fill="var(--white)" d="M2.5 1 L4.5 1 L5.3 3.4 L4 4.4 C4.6 5.8 6.2 7.4 7.6 8 L8.6 6.7 L11 7.5 L11 9.5 C11 10.3 10.3 11 9.5 11 C5 11 1 7 1 2.5 C1 1.7 1.7 1 2.5 1 Z"/></svg>
      </li>
      <li class="contact-list__item">info@yourmail.com
        <svg class="contact-list__icon" viewBox="0 0 12 12" aria-hidden="true"><rect x="1" y="2.5" width="10" height="7" fill="var(--white)"/><path d="M1 2.5 L6 6.5 L11 2.5" fill="none" stroke="var(--navy)" stroke-width="1"/></svg>
      </li>
      <li class="contact-list__item">www.yourwebsite.com
        <svg class="contact-list__icon" viewBox="0 0 12 12" aria-hidden="true"><circle cx="6" cy="6" r="5" fill="none" stroke="var(--white)" stroke-width="1.2"/><ellipse cx="6" cy="6" rx="2" ry="5" fill="none" stroke="var(--white)" stroke-width="1"/><line x1="1" y1="6" x2="11" y2="6" stroke="var(--white)" stroke-width="1"/></svg>
      </li>
    </ul>
  </section>

  <!-- Brand side -->
  <section class="card card--brand" aria-label="Business card, brand side">
    <div class="brand-name">
      <span class="brand-name__mark" aria-hidden="true"></span>
      <span class="brand-name__text">Meridian Service Reps</span>
    </div>
    <div class="social-row" aria-label="Social media links">
      <span class="social-row__dot"></span>
      <span class="social-row__dot"></span>
      <span class="social-row__dot"></span>
      <span class="social-row__dot"></span>
      <span class="social-row__dot"></span>
      <span class="social-row__dot"></span>
    </div>
  </section>

</main>
</body>
</html>
```